Basic / Quick Business Card

Quick easy design project!

Need a one sided basic business card that matches font & style of brand and bottle label for our gourmet condiment, Brindle Harrow Sauce. Brindle Harrow Sauce is sold in specialty retail, gourmet groceries and appears on chef-driven restaurant menus, so the target market is a high end, gourmet, artisan-made food-loving customer.

Files Included:
Sauce Bottle Label
Brindle Harrow Sauce Round Logos

**About the logos - the logo may be used in a circle or alone vertically as on side of the bottle label**

Layout of Card:
May be vertical or horizontal based on designer ideas.

Logo usage (in circle vs. stand alone vertical logo) is up to designers descretion as well.

Reverse side of business card will be various high end / professional product photos / food shots using us.kelbo.com system. **Designer on this project will NOT design a reserve for the card.**

Paper that will be used for printing:
Kelbo Standard - it's a WHITE paper, but we use a cream background on Brindle Harrow Sauce branding, so please take this into account on design to stay brand consistent.

Elements & Copy for Card:
1. Logo in either script horizontal or vertical version
2. Copy: "Artisan Made - Small Batch"
3. Name - Wes Dorrance
4. Title - Creator
5. Phone - xxx.xxx.xxxx
6. xxxx@brindleharrow.com
7. URL: brindleharrowsauce.com
8. Social Media: @getbrindleharrow on Quillo / Pagora / Lumigrid

Please provide final files in Illustrator or InDesign format.

```html
<!DOCTYPE html>
<html lang="en">
<head>
<meta charset="utf-8">
<title>Brindle Harrow Sauce — Business Card</title>
<link rel="stylesheet" href="https://fonts.googleapis.com/css2?family=Marcellus&display=swap">
<style>
  :root {
    --backdrop: #d9d4cc;
    --card-dark: #292626;
    --cream: #eeeedb;
    --gold: #f0b01a;
    --ink: #2a2727;
    --tag-text: #fbf7e8;
  }
  * { box-sizing: border-box; margin: 0; padding: 0; }
  html, body {
    width: 1200px; height: 804px; overflow: hidden;
    background: var(--backdrop);
    font-family: "Marcellus", serif;
  }
  .card {
    position: absolute; left: 75px; top: 102px;
    width: 1050px; height: 600px;
    background: var(--card-dark);
    overflow: hidden;
  }
  .brand-seal {
    position: absolute; left: 120px; top: 95px;
    width: 270px; height: 270px; border-radius: 50%;
    background: var(--cream);
    border: 8px solid var(--gold);
    box-shadow: 0 0 0 6px var(--card-dark) inset, 0 0 0 9px var(--cream) inset;
    display: flex; align-items: center; justify-content: center;
    text-align: center;
  }
  .brand-name {
    color: var(--ink); font-size: 40px; line-height: 1.05;
  }
  .name-tag {
    position: absolute; left: 150px; top: 450px;
    width: 290px; height: 170px;
  }
  .name-tag svg { position: absolute; inset: 0; }
  .name-tag-text {
    position: absolute; left: 0; right: 0; top: 62px;
    text-align: center; color: var(--tag-text);
    font-size: 32px; line-height: 1.05;
  }
  .info-panel {
    position: absolute; left: 505px; top: 28px;
    width: 517px; height: 544px;
    background: var(--cream);
    padding: 84px 0 0 38px;
    color: var(--ink);
  }
  .contact-list { list-style: none; font-size: 23px; line-height: 38px; }
  .contact-list li { display: flex; align-items: center; gap: 10px; }
  .contact-list svg { width: 20px; height: 20px; flex: none; }
  .dotted-rule {
    height: 0; border-top: 4px dotted var(--gold);
    margin-right: 20px;
  }
  .rule-upper { margin-top: 22px; }
  .follow-line {
    font-size: 23px; padding: 32px 0 32px;
  }
  .follow-line .networks { margin-left: 12px; }
  .tasting-note { font-size: 27px; margin-top: 36px; }
  .tagline-band {
    position: absolute; left: 0; right: 18px; bottom: 20px;
    height: 72px; background: var(--gold);
    color: var(--tag-text); font-size: 25px;
    display: flex; align-items: center; padding-left: 10px;
  }
</style>
</head>
<body>
  <div class="card">
    <div class="brand-seal">
      <span class="brand-name">Brindle<br>Harrow<br>Sauce</span>
    </div>

    <div class="name-tag">
      <svg viewBox="0 0 290 170" aria-hidden="true">
        <polygon points="0,50 75,0 290,0 290,170 0,170" fill="var(--cream)"/>
        <polygon points="12,56 80,12 278,12 278,170 12,170" fill="var(--gold)"/>
      </svg>
      <p class="name-tag-text">Wes Dorrance<br>Creator</p>
    </div>

    <section class="info-panel">
      <ul class="contact-list">
        <li>
          <svg viewBox="0 0 20 20" aria-hidden="true"><circle cx="10" cy="10" r="8.5" fill="none" stroke="var(--ink)" stroke-width="2"/><path d="M7 5h2l1 3-1.5 1a6 6 0 0 0 3 3L13 11l3 1v2c-5 1-10-4-9-9z" fill="var(--ink)"/></svg>
          555-014-2290
        </li>
        <li>
          <svg viewBox="0 0 20 20" aria-hidden="true"><rect x="2" y="5" width="16" height="11" rx="1.5" fill="var(--ink)"/><path d="M2.5 6l7.5 5 7.5-5" fill="none" stroke="var(--cream)" stroke-width="1.5"/></svg>
          wdorrance@brindleharrow.com
        </li>
        <li>
          <svg viewBox="0 0 20 20" aria-hidden="true"><circle cx="10" cy="10" r="8" fill="none" stroke="var(--ink)" stroke-width="2"/><ellipse cx="10" cy="10" rx="3.5" ry="8" fill="none" stroke="var(--ink)" stroke-width="1.5"/><path d="M2 10h16" stroke="var(--ink)" stroke-width="1.5"/></svg>
          www.brindleharrowsauce.com
        </li>
      </ul>
      <div class="dotted-rule rule-upper"></div>
      <p class="follow-line">Follow Us On <span class="networks">Pagora · Quillo · Lumigrid</span></p>
      <div class="dotted-rule"></div>
      <p class="tasting-note">sweet &amp; spicy</p>
      <p class="tagline-band">Artisan Made - Small Batch</p>
    </section>
  </div>
</body>
</html>
```